Business Card Design Project

i need a bussines car design
Velora Clinical Hypnotherapy

Daniel Wexford
Psychotherapy & Hypnosis

84261937 /0427591628

back of the card appoinment space.

file was provided on a PDF, LOgo , use the blu colorsa as well , elegant, clear,

Target Market(s)

young professional, caucasian , young mothers.

Industry/Entity Type

Business

```html
<!DOCTYPE html>
<html lang="en">
<head>
<meta charset="utf-8">
<title>Velora Clinical Hypnotherapy – Business Card</title>
<link rel="stylesheet" href="https://fonts.googleapis.com/css2?family=Questrial&family=Open+Sans:wght@400;600;700&display=swap">
<style>
  :root {
    --blue: #3a78c2;
    --blue-light: #5b95d6;
    --ink: #3b3b3b;
    --ink-soft: #555555;
    --paper: #ffffff;
    --stage: #e9ebee;
    --rule: #9a9a9a;
  }
  * { box-sizing: border-box; margin: 0; padding: 0; }
  html, body { width: 1200px; height: 800px; overflow: hidden; }
  body {
    background: var(--stage);
    font-family: "Questrial", "Open Sans", sans-serif;
    color: var(--ink);
    position: relative;
  }
  .card {
    position: absolute;
    top: 250px;
    width: 525px;
    height: 300px;
    background: var(--paper);
    box-shadow: 0 6px 18px rgba(0,0,0,0.12);
    overflow: hidden;
  }
  .card--front { left: 50px; }
  .card--back { left: 625px; }

  /* Front */
  .brand { position: absolute; left: 95px; top: 32px; width: 390px; }
  .brand__name {
    display: flex; align-items: center; gap: 9px;
    font-size: 23px; color: var(--blue); line-height: 1; white-space: nowrap;
  }
  .brand__dot { width: 14px; height: 14px; border-radius: 50%; background: var(--blue); flex: none; }
  .brand__rule { height: 1.5px; background: var(--blue); margin: 8px 0 5px; }
  .brand__web { font-size: 11px; letter-spacing: 0.9px; color: var(--ink); white-space: nowrap; }

  .person { position: absolute; right: 40px; top: 125px; text-align: right; }
  .person__name { font-family: "Open Sans", sans-serif; font-weight: 700; font-size: 17px; color: var(--ink); letter-spacing: 0.3px; }
  .person__role { font-size: 13px; color: var(--ink-soft); margin-top: 2px; }

  .contact { position: absolute; right: 40px; top: 192px; text-align: right; font-size: 14px; line-height: 1.5; color: var(--ink); }
  .contact b { font-family: "Open Sans", sans-serif; font-weight: 700; font-size: 13px; }

  .clinic { position: absolute; left: 40px; top: 218px; color: var(--blue); }
  .clinic__label { font-family: "Open Sans", sans-serif; font-weight: 700; font-size: 14px; margin-left: 64px; }
  .clinic__address { font-size: 15px; margin-top: 4px; white-space: nowrap; }

  .band { position: absolute; left: 0; right: 0; bottom: 0; height: 16px; background: linear-gradient(90deg, var(--blue), var(--blue-light)); }

  /* Back */
  .card--back { padding: 26px 28px; display: flex; justify-content: space-between; }
  .appts { width: 220px; }
  .appts__title { font-family: "Open Sans", sans-serif; font-weight: 700; font-size: 14px; margin-bottom: 14px; }
  .appts__row { display: flex; align-items: flex-end; gap: 6px; font-size: 10px; color: var(--ink-soft); height: 38px; }
  .appts__num { width: 10px; }
  .appts__line { border-bottom: 1px solid var(--rule); height: 1px; }
  .appts__date { width: 60px; }
  .appts__time { width: 70px; }

  .practice { width: 235px; text-align: right; font-family: "Open Sans", sans-serif; }
  .practice__name { font-weight: 700; font-size: 11px; letter-spacing: 2.4px; text-transform: uppercase; color: var(--ink); line-height: 1.5; }
  .practice__line { font-size: 10px; color: var(--ink); line-height: 1.7; white-space: nowrap; }
  .practice__reg { font-weight: 600; font-size: 10px; margin-top: 18px; }
  .practice__note { font-size: 7.5px; color: var(--ink-soft); line-height: 1.5; margin-top: 6px; }
</style>
</head>
<body>
  <section class="card card--front" aria-label="Card front">
    <div class="brand">
      <div class="brand__name"><span class="brand__dot"></span>Velora Clinical Hypnotherapy</div>
      <div class="brand__rule"></div>
      <div class="brand__web">www.veloraclinicalhypnotherapy.com.au</div>
    </div>
    <div class="person">
      <div class="person__name">DANIEL WEXFORD</div>
      <div class="person__role">Psychotherapy &amp; Hypnosis</div>
    </div>
    <div class="contact">
      <div><b>Mobile:</b> 0427 591 628</div>
      <div><b>Phone:</b> 842 61 937</div>
    </div>
    <div class="clinic">
      <div class="clinic__label">Clinic Address:</div>
      <div class="clinic__address">148 Harlow Street, Kensington Vale</div>
    </div>
    <div class="band"></div>
  </section>

  <section class="card card--back" aria-label="Card back">
    <div class="appts">
      <div class="appts__title">Your Appointments</div>
      <div class="appts__row"><span class="appts__num">1.</span><span class="appts__line appts__date"></span><span class="appts__line appts__time"></span>am/pm</div>
      <div class="appts__row"><span class="appts__num">2.</span><span class="appts__line appts__date"></span><span class="appts__line appts__time"></span>am/pm</div>
      <div class="appts__row"><span class="appts__num">3.</span><span class="appts__line appts__date"></span><span class="appts__line appts__time"></span>am/pm</div>
      <div class="appts__row"><span class="appts__num">4.</span><span class="appts__line appts__date"></span><span class="appts__line appts__time"></span>am/pm</div>
      <div class="appts__row"><span class="appts__num">5.</span><span class="appts__line appts__date"></span><span class="appts__line appts__time"></span>am/pm</div>
    </div>
    <div class="practice">
      <div class="practice__name">Velora Clinical Hypnotherapy</div>
      <div class="practice__line">By Appointment: Phone: 0427 591 628</div>
      <div class="practice__line">62 Marden Lane, Ashbury 3021</div>
      <div class="practice__line">hello@veloraclinicalhypnotherapy.com.au</div>
      <div class="practice__reg">NHRA Registration No. NPM058217</div>
      <div class="practice__note">To reschedule your appointment, please SMS or phone 0427 591 628 at least 24 hours prior to your allocated time. Thank you.</div>
    </div>
  </section>
</body>
</html>
```